Music Quizz Application

Hello,

I want a new design for my Blind test (music quizz) application on Korvex. You will find attached the images I want to replace. I need something with the same element (menu / song title) but with a different look!

Same, new icon, you have carte blanche to this one.

I am looking for something fresh…. I'm looking for something with a real artistic choice, contrast, colours, etc.

As a marketing screenshot, I want something classic, you'll find an example attached, feel free to innovate.

To sum-up :

- One new view for my App
- One new icon
- One marketing screenshot

screen resolution :
640×960
icon resolution :
1024x1024

Target Market(s)

15-30 years

Industry/Entity Type

Marketing

```html
<!DOCTYPE html>
<html lang="en">
<head>
<meta charset="utf-8">
<title>Tunequest – Home</title>
<link rel="stylesheet" href="https://fonts.googleapis.com/css2?family=Ubuntu:wght@300;400;500&family=Arimo:wght@700&display=swap">
<style>
  :root {
    --status-bg: #000000;
    --status-text: #d9d9d9;
    --wordmark: #2a2623;
    --menu-top: #444342;
    --menu-bottom: #1a1613;
    --menu-text: #f4f1ec;
    --divider-dark: #0d0b0a;
    --divider-light: rgba(255,255,255,0.22);
    --teal: #4fb8a8;
    --yellow: #ffe94a;
    --orange: #d98a2a;
    --glow: #fffdf2;
    --shade: #14120f;
  }
  * { margin: 0; padding: 0; box-sizing: border-box; }
  html, body { width: 800px; height: 1200px; overflow: hidden; background: var(--shade); }
  .screen { position: relative; width: 800px; height: 1200px; overflow: hidden; }

  .status-bar {
    position: absolute; top: 0; left: 0; width: 800px; height: 50px;
    background: var(--status-bg); color: var(--status-text);
    font-family: "Arimo", Arial, sans-serif; font-weight: 700; font-size: 27px;
    z-index: 2;
  }
  .status-bar .carrier { position: absolute; left: 10px; top: 10px; display: flex; align-items: center; gap: 14px; }
  .status-bar .signal { display: flex; align-items: flex-end; gap: 3px; height: 20px; }
  .status-bar .signal i { display: block; width: 5px; height: 3px; background: var(--status-text); }
  .status-bar .signal i.on { height: 8px; width: 6px; }
  .status-bar .network { font-size: 25px; margin-left: 6px; }
  .status-bar .clock { position: absolute; left: 0; right: 0; top: 10px; text-align: center; }
  .status-bar .power { position: absolute; right: 10px; top: 10px; display: flex; align-items: center; gap: 12px; }

  .backdrop {
    position: absolute; inset: 50px 0 0 0;
    background:
      radial-gradient(ellipse 260px 300px at 400px 620px, var(--glow) 0%, rgba(255,253,242,0) 100%),
      radial-gradient(ellipse 280px 260px at 640px 380px, var(--yellow) 0%, rgba(255,233,74,0) 100%),
      radial-gradient(ellipse 150px 120px at 700px 150px, var(--orange) 0%, rgba(217,138,42,0) 100%),
      radial-gradient(ellipse 200px 330px at 10px 450px, var(--teal) 0%, rgba(79,184,168,0) 100%),
      radial-gradient(ellipse 260px 200px at 60px 120px, #1f2a22 0%, rgba(31,42,34,0) 100%),
      radial-gradient(ellipse 420px 260px at 380px 1150px, #0c0a08 0%, rgba(12,10,8,0) 100%),
      linear-gradient(180deg, #6f6a48 0%, #c9c38a 35%, #d8d2a0 55%, #6a6540 80%, #221d16 100%);
  }

  .brand {
    position: absolute; left: 0; right: 0; top: 545px;
    text-align: center; z-index: 1;
    font-family: "Ubuntu", sans-serif; font-weight: 300; font-size: 108px;
    letter-spacing: 1px; color: var(--wordmark); line-height: 1;
  }

  .main-menu {
    position: absolute; left: 157px; top: 737px; width: 487px; height: 278px;
    border-radius: 5px; z-index: 1;
    background: linear-gradient(180deg, var(--menu-top) 0%, #2a2623 45%, var(--menu-bottom) 100%);
    box-shadow: 0 2px 4px rgba(0,0,0,0.5), inset 0 1px 0 rgba(255,255,255,0.12);
    list-style: none;
    font-family: "Ubuntu", sans-serif; font-weight: 500; font-size: 24px; color: var(--menu-text);
  }
  .main-menu li { position: absolute; left: 0; right: 0; text-align: center; line-height: 30px; }
  .main-menu .quick { top: 40px; }
  .main-menu .blind { top: 130px; }
  .main-menu .challenge { top: 214px; }
  .main-menu .divider {
    position: absolute; left: 62px; width: 363px; height: 2px;
    border-top: 1px solid var(--divider-dark); border-bottom: 1px solid var(--divider-light);
  }
  .main-menu .d1 { top: 96px; }
  .main-menu .d2 { top: 181px; }
</style>
</head>
<body>
<div class="screen">
  <header class="status-bar">
    <div class="carrier">
      <span class="signal"><i class="on"></i><i></i><i></i><i></i><i></i></span>
      <span>Nuvo</span><span class="network">3G</span>
    </div>
    <div class="clock">12:14</div>
    <div class="power">
      <svg width="16" height="28" viewBox="0 0 16 28" aria-label="Bluetooth">
        <path d="M2 8 L13 19 L7.5 24 V4 L13 9 L2 20" fill="none" stroke="#6f6f6f" stroke-width="2.5" stroke-linejoin="round"/>
      </svg>
      <span>89 %</span>
      <svg width="40" height="24" viewBox="0 0 40 24" aria-label="Battery charging">
        <rect x="1.5" y="2.5" width="32" height="19" rx="3" fill="none" stroke="#d9d9d9" stroke-width="2.5"/>
        <rect x="34" y="8" width="4" height="8" rx="1" fill="#d9d9d9"/>
        <rect x="5" y="6" width="25" height="12" fill="#d9d9d9"/>
        <path d="M19 3 L12 13 H18 L15 21 L24 10 H18 Z" fill="#000"/>
      </svg>
    </div>
  </header>

  <div class="backdrop" role="img" aria-label="Soft blurred background of teal, yellow and warm light"></div>

  <h1 class="brand">Tunequest</h1>

  <ul class="main-menu">
    <li class="quick">Quick Game</li>
    <span class="divider d1"></span>
    <li class="blind">Blind Test</li>
    <span class="divider d2"></span>
    <li class="challenge">Challenge</li>
  </ul>
</div>
</body>
</html>
```